At Home Pet Euthanasia - business cards & brand stationary

We already have a logo and the colors and a website. Need a business card designed that will be able to customized to multiple veterinarians who will be partnering with us. The feel needs to be compassionate, comforting with our tagline 'A Gift of Love at Home'. It will be 2 sides.
On the back our platform/partner vets will be customizing each business card with their own service areas, phone numbers, name and title. On the front, i would like to see experimentation with use of our photos, the logo, tagline and a description 'Peaceful and Compassionate At-Home Pet Euthanasia'

```html
<!DOCTYPE html>
<html lang="en">
<head>
<meta charset="utf-8">
<title>Stillwater Pet – Business Card</title>
<link href="https://fonts.googleapis.com/css2?family=Lato:wght@400;700&family=Oswald:wght@500&family=Quicksand:wght@500&family=Playfair+Display:ital@1&display=swap" rel="stylesheet">
<style>
  :root {
    --backdrop: #2a2a2c;
    --card: #111113;
    --accent: #7896c0;
    --ink: #ffffff;
    --rule: #6f6f74;
  }
  * { margin: 0; padding: 0; box-sizing: border-box; }
  html, body { width: 1200px; height: 900px; overflow: hidden; }
  body {
    background: var(--backdrop);
    display: flex;
    flex-direction: column;
    align-items: center;
    justify-content: center;
    gap: 44px;
    font-family: "Lato", sans-serif;
  }
  .card {
    position: relative;
    width: 640px;
    height: 366px;
    background: var(--card);
    box-shadow: 0 10px 30px rgba(0,0,0,.55);
    overflow: hidden;
  }
  .card__band {
    position: absolute;
    left: 0; right: 0; bottom: 0;
    height: 11px;
    background: var(--accent);
  }

  /* Front */
  .brand {
    position: absolute;
    left: 190px;
    top: 92px;
    display: flex;
    align-items: center;
    gap: 18px;
  }
  .brand__mark {
    width: 58px; height: 58px;
    background: var(--accent);
  }
  .brand__name {
    font-family: "Lato", sans-serif;
    font-weight: 700;
    font-size: 56px;
    color: var(--accent);
    line-height: 1;
  }
  .brand__tagline {
    position: absolute;
    left: 300px;
    top: 172px;
    font-family: "Quicksand", sans-serif;
    font-weight: 500;
    font-size: 21px;
    color: var(--accent);
  }
  .front__description {
    position: absolute;
    left: 0; right: 0;
    bottom: 34px;
    text-align: center;
    font-family: "Playfair Display", serif;
    font-style: italic;
    font-size: 21px;
    color: var(--accent);
  }

  /* Back */
  .person {
    position: absolute;
    left: 70px;
    top: 108px;
    width: 230px;
    text-align: right;
  }
  .person__name {
    font-family: "Oswald", sans-serif;
    font-weight: 500;
    font-size: 34px;
    color: var(--accent);
    text-transform: uppercase;
    letter-spacing: -.5px;
    line-height: 1.1;
  }
  .person__title {
    font-size: 19px;
    color: var(--ink);
  }
  .divider {
    position: absolute;
    left: 318px;
    top: 104px;
    width: 1px;
    height: 102px;
    background: var(--rule);
  }
  .contacts {
    position: absolute;
    left: 338px;
    top: 112px;
    list-style: none;
  }
  .contacts li {
    display: flex;
    align-items: center;
    gap: 10px;
    font-size: 19px;
    color: var(--ink);
    line-height: 28px;
  }
  .contacts svg { width: 18px; height: 18px; fill: none; stroke: var(--ink); stroke-width: 1.6; }
  .address {
    position: absolute;
    left: 70px;
    bottom: 40px;
    font-size: 19px;
    color: var(--ink);
  }
</style>
</head>
<body>

  <section class="card card--front">
    <div class="brand">
      <span class="brand__mark"></span>
      <span class="brand__name">Stillwater Pet</span>
    </div>
    <p class="brand__tagline">A gift of love at home.</p>
    <p class="front__description">Peaceful and Compassionate At-Home Pet Euthanasia</p>
    <div class="card__band"></div>
  </section>

  <section class="card card--back">
    <div class="person">
      <h1 class="person__name">Daniel Reyes</h1>
      <p class="person__title">Managing Director</p>
    </div>
    <div class="divider"></div>
    <ul class="contacts">
      <li>
        <svg viewBox="0 0 24 24" aria-hidden="true"><path d="M5 3h4l2 5-3 2a11 11 0 0 0 6 6l2-3 5 2v4a2 2 0 0 1-2 2A17 17 0 0 1 3 5a2 2 0 0 1 2-2z"/></svg>
        044-555 010 203
      </li>
      <li>
        <svg viewBox="0 0 24 24" aria-hidden="true"><rect x="2" y="5" width="20" height="14"/><path d="M2 5l10 8 10-8"/></svg>
        hello@stillwaterpet.com
      </li>
      <li>
        <svg viewBox="0 0 24 24" aria-hidden="true"><circle cx="12" cy="12" r="10"/><ellipse cx="12" cy="12" rx="4" ry="10"/><path d="M2 12h20M4 7h16M4 17h16"/></svg>
        www.stillwaterpet.com
      </li>
    </ul>
    <p class="address">421, Address line here, Country Name, 45452</p>
    <div class="card__band"></div>
  </section>

</body>
</html>
```